Stylish Business Cards Wanted

- DOUBLE SIDED Design Required -

High end, edgy cards for a corporate and personal stylist. Must include logo,
Name: Belinda Harwick
Title: Director and Stylist
telephone : +61 8 7142 5809
email: belinda@theloombriefing.example
website: theloombriefing.example
Tag: Corporate Workwear & Uniform Specialist | Personal Stylist
Would like nice icons for telephone, email, website

Target Market(s)

Businesses wanting stylish uniforms, people wanting stylish wardrobes

Industry/Entity Type

Corporate Workwear Stylist

Contact Information for Business Card

I would like black, white and gold foiling incorporated in the design - possibly a touch of the other colours on my branding guide attached Name: Belinda Harwick Title: Director and Stylist telephone : +61 8 7142 5809 email: belinda@theloombriefing.example website: theloombriefing.example Tag: Corporate Workwear & Uniform Specialist | Personal Stylist Would like nice icons for telephone, email, website

Font styles to use
Other font styles liked:
• Raleway

Colors

Designer to choose colors to be used in the design.

Requirements
Must have
• Gold foil accents

```html
<!DOCTYPE html>
<html lang="en">
<head>
<meta charset="utf-8">
<title>The Loom Briefing – Business Cards</title>
<link rel="stylesheet" href="https://fonts.googleapis.com/css2?family=Arimo:wght@400&family=Berkshire+Swash&display=swap">
<style>
  :root {
    --backdrop: #9c9c9c;
    --ink: #231f20;
    --paper: #ffffff;
    --gold: #e5bd58;
    --mist: #dfe3e2;
    --rule: #8a8a8a;
  }
  * { margin: 0; padding: 0; box-sizing: border-box; }
  html, body {
    width: 1200px;
    height: 1200px;
    overflow: hidden;
    background: var(--backdrop);
    font-family: "Arimo", Arial, sans-serif;
  }
  .stage {
    position: relative;
    width: 1200px;
    height: 1200px;
  }
  .card {
    position: absolute;
    top: 303px;
    width: 368px;
    height: 594px;
  }
  .card--front { left: 201px; background: var(--ink); }
  .card--back { left: 599px; background: var(--paper); }

  .brand-name {
    position: absolute;
    left: 0;
    right: 0;
    text-align: center;
    font-family: "Arimo", Arial, sans-serif;
    font-weight: 400;
    font-size: 40px;
    line-height: 1.15;
    letter-spacing: 1px;
  }
  .card--front .brand-name { top: 180px; color: var(--mist); }
  .card--back .brand-name { top: 118px; color: var(--ink); font-size: 36px; }

  .tag-band {
    position: absolute;
    left: 0;
    right: 0;
    top: 496px;
    height: 49px;
    background: var(--gold);
    color: var(--ink);
    font-size: 16px;
    line-height: 21px;
    text-align: center;
    padding-top: 4px;
  }

  .person {
    position: absolute;
    left: 0;
    right: 0;
    top: 392px;
    text-align: center;
  }
  .person__name {
    font-family: "Berkshire Swash", cursive;
    font-size: 27px;
    color: var(--ink);
    line-height: 32px;
  }
  .person__title {
    font-size: 15px;
    color: var(--gold);
    letter-spacing: 0.5px;
    line-height: 20px;
  }

  .icon-row {
    position: absolute;
    left: 87px;
    top: 459px;
    width: 190px;
    height: 25px;
    display: flex;
    align-items: center;
    gap: 4px;
  }
  .icon-row__rule {
    flex: 1;
    height: 1px;
    background: var(--rule);
    margin: 0 4px;
  }
  .icon-tile {
    width: 25px;
    height: 25px;
    border-radius: 3px;
    background: var(--ink);
    display: flex;
    align-items: center;
    justify-content: center;
  }

  .contact {
    position: absolute;
    left: 0;
    right: 0;
    top: 492px;
    text-align: center;
    font-size: 16.5px;
    line-height: 22px;
    color: var(--ink);
  }
</style>
</head>
<body>
<main class="stage">

  <section class="card card--front" aria-label="Business card front">
    <p class="brand-name">The Loom<br>Briefing</p>
    <p class="tag-band">Corporate Workwear &amp; Uniform Specialist<br>Personal Stylist</p>
  </section>

  <section class="card card--back" aria-label="Business card back">
    <p class="brand-name">The Loom<br>Briefing</p>

    <div class="person">
      <p class="person__name">Belinda Harwick</p>
      <p class="person__title">DIRECTOR AND STYLIST</p>
    </div>

    <div class="icon-row">
      <span class="icon-row__rule"></span>
      <span class="icon-tile" aria-label="Telephone">
        <svg width="17" height="17" viewBox="0 0 24 24" fill="none" stroke="#fff" stroke-width="2" stroke-linecap="round" stroke-linejoin="round">
          <path d="M3 9c0-3 4-4 9-4s9 1 9 4v1h-4V8H7v2H3z"/>
          <rect x="6" y="11" width="12" height="9" rx="1"/>
          <circle cx="12" cy="15.5" r="2"/>
        </svg>
      </span>
      <span class="icon-tile" aria-label="Email">
        <svg width="17" height="17" viewBox="0 0 24 24" fill="none" stroke="#fff" stroke-width="2" stroke-linejoin="round">
          <rect x="3" y="6" width="18" height="12"/>
          <path d="M3 6l9 7 9-7M3 18l7-6M21 18l-7-6"/>
        </svg>
      </span>
      <span class="icon-tile" aria-label="Website">
        <svg width="17" height="17" viewBox="0 0 24 24" fill="none" stroke="#fff" stroke-width="2">
          <circle cx="12" cy="12" r="8"/>
          <path d="M4 12h16M12 4c3 3 3 13 0 16M12 4c-3 3-3 13 0 16"/>
        </svg>
      </span>
      <span class="icon-row__rule"></span>
    </div>

    <address class="contact" style="font-style:normal">
      +61 8 7142 5809<br>
      belinda@theloombriefing.example<br>
      theloombriefing.example
    </address>
  </section>

</main>
</body>
</html>
```